Coastline Premier Retreats Business Card Design

Design a business card for Coastline Premier Retreats. Look at the website for colors and reference. Card should have logo, name, title, office number, mobile number, email, URL and a tagline like, "Luxury Hotel & Resort Email Marketing" (This might change).

https://www.coastlinepremierretreats.example

The rest I will leave up to your imagination.

Contact Information for Business Card

Logo, name, title, office number, mobile number, email, URL and a tagline like, "Luxury Hotel & Resort Email Marketing" (This might change).

```html
<!DOCTYPE html>
<html lang="en">
<head>
<meta charset="utf-8">
<title>Coastline Premier Retreats – Business Card</title>
<link rel="stylesheet" href="https://fonts.googleapis.com/css2?family=Open+Sans:wght@400;600;700&display=swap">
<style>
  :root {
    --backdrop: #232323;
    --card-dark: #222226;
    --brand-orange: #f47321;
    --orange-deep: #d65e12;
    --ink-light: #ffffff;
    --card-w: 540px;
    --card-h: 309px;
  }
  * { box-sizing: border-box; margin: 0; padding: 0; }
  html, body {
    width: 1200px; height: 780px; overflow: hidden;
    background: var(--backdrop);
    font-family: "Open Sans", Arial, sans-serif;
  }
  .card-sheet {
    position: relative;
    width: 1200px; height: 780px;
    display: flex; align-items: center; justify-content: space-between;
    padding: 0 40px;
  }
  .card {
    position: relative;
    width: var(--card-w); height: var(--card-h);
    overflow: hidden;
    box-shadow: 0 14px 30px rgba(0,0,0,.45);
  }
  /* front */
  .card-front { background: var(--card-dark); color: var(--ink-light); }
  .front-swoosh { position: absolute; inset: 0; width: 100%; height: 100%; }
  .holder-name {
    position: absolute; left: 52px; top: 52px;
    font-size: 24px; font-weight: 700; letter-spacing: .2px;
  }
  .holder-name .first { color: var(--brand-orange); }
  .holder-title {
    position: absolute; left: 82px; top: 86px;
    font-size: 12.5px; font-weight: 400;
  }
  .divider {
    position: absolute; left: 262px; top: 130px;
    width: 1.5px; height: 78px; background: var(--ink-light);
  }
  .contact-list {
    position: absolute; left: 276px; top: 128px;
    list-style: none; font-size: 12px; line-height: 20px;
  }
  .contact-list li { display: flex; align-items: center; gap: 8px; }
  .contact-list svg { width: 12px; height: 12px; flex: none; }
  .brand-lockup {
    position: absolute; right: 34px; top: 34px;
    display: flex; align-items: center; gap: 10px;
  }
  .brand-mark { width: 14px; height: 14px; background: var(--brand-orange); }
  .brand-name {
    font-size: 19px; font-weight: 700; line-height: 1.1;
    text-transform: uppercase; letter-spacing: 1px; color: var(--ink-light);
  }
  .tagline {
    position: absolute; left: 26px; bottom: 10px;
    font-size: 12.5px; font-weight: 400; color: var(--ink-light);
  }
  /* back */
  .card-back {
    background: var(--brand-orange);
    display: flex; align-items: center; justify-content: center;
  }
  .back-brand {
    font-size: 30px; font-weight: 700; line-height: 1.15;
    text-transform: uppercase; letter-spacing: 2px; text-align: center;
    color: var(--orange-deep);
  }
</style>
</head>
<body>
<main class="card-sheet">

  <section class="card card-front" aria-label="Business card front">
    <svg class="front-swoosh" viewBox="0 0 540 309" preserveAspectRatio="none" aria-hidden="true">
      <path d="M0,196 C70,296 270,300 540,236 L540,309 L0,309 Z" fill="var(--brand-orange)"/>
      <path d="M14,178 C80,290 280,298 532,232 C290,292 88,282 18,182 Z" fill="var(--ink-light)"/>
    </svg>

    <div class="brand-lockup">
      <span class="brand-mark"></span>
      <span class="brand-name">Coastline<br>Premier Retreats</span>
    </div>

    <h1 class="holder-name"><span class="first">Marisa</span> Delvane</h1>
    <p class="holder-title">Managing Director</p>

    <span class="divider"></span>

    <ul class="contact-list">
      <li>
        <svg viewBox="0 0 24 24"><path fill="var(--brand-orange)" d="M6.6 10.8a15 15 0 0 0 6.6 6.6l2.2-2.2c.3-.3.7-.4 1-.2 1.1.4 2.3.6 3.6.6.6 0 1 .4 1 1V20c0 .6-.4 1-1 1A17 17 0 0 1 3 4c0-.6.4-1 1-1h3.5c.6 0 1 .4 1 1 0 1.3.2 2.5.6 3.6.1.3 0 .7-.2 1z"/></svg>
        (555) 014-2758
      </li>
      <li>
        <svg viewBox="0 0 24 24"><rect x="6" y="2" width="12" height="20" rx="2" fill="none" stroke="var(--brand-orange)" stroke-width="2"/><circle cx="12" cy="18" r="1.2" fill="var(--brand-orange)"/></svg>
        (555) 019-7777
      </li>
      <li>
        <svg viewBox="0 0 24 24"><circle cx="12" cy="12" r="9" fill="none" stroke="var(--brand-orange)" stroke-width="2"/><path d="M3 12h18M12 3c3 3 3 15 0 18M12 3c-3 3-3 15 0 18" fill="none" stroke="var(--brand-orange)" stroke-width="1.6"/></svg>
        www.coastlinepremierretreats.example
      </li>
      <li>
        <svg viewBox="0 0 24 24"><rect x="2" y="5" width="20" height="14" rx="1.5" fill="var(--brand-orange)"/><path d="M3 6l9 7 9-7" fill="none" stroke="var(--card-dark)" stroke-width="1.6"/></svg>
        info@coastlinepremierretreats.example
      </li>
    </ul>

    <p class="tagline">Luxury Hotel &amp; Resort Email Marketing</p>
  </section>

  <section class="card card-back" aria-label="Business card back">
    <p class="back-brand">Coastline<br>Premier Retreats</p>
  </section>

</main>
</body>
</html>
```